Business card for event manager / organizer "waiter service"

Draft of a new valuable business card for my company.
Events, personnel service providers, festivals

```html
<!DOCTYPE html>
<html lang="de">
<head>
<meta charset="utf-8">
<title>Falkos Kellnerservice – Visitenkarte</title>
<link rel="stylesheet" href="https://fonts.googleapis.com/css2?family=Poppins:wght@200;300;400;600;800&display=swap">
<style>
  :root {
    --stage: #3a3a3c;
    --card: #262326;
    --orange: #f07d1f;
    --white: #ffffff;
    --muted: #d9d9d9;
    --photo-light: #b9b8bb;
    --photo-mid: #6b6a6e;
  }
  * { box-sizing: border-box; margin: 0; padding: 0; }
  html, body { width: 1200px; height: 900px; overflow: hidden; }
  body {
    background: var(--stage);
    font-family: "Poppins", sans-serif;
    color: var(--white);
    display: flex;
    flex-direction: column;
    align-items: center;
    justify-content: center;
    gap: 40px;
  }
  .card {
    position: relative;
    width: 640px;
    height: 366px;
    background: var(--card);
    border-radius: 18px;
    overflow: hidden;
    box-shadow: 0 10px 30px rgba(0,0,0,.35);
  }

  /* Brand block */
  .brand { position: absolute; display: flex; align-items: center; }
  .brand__mark { background: var(--orange); flex: none; }
  .brand__text { display: flex; flex-direction: column; }
  .brand__name {
    font-weight: 800;
    color: var(--white);
    text-transform: uppercase;
    line-height: 1;
    letter-spacing: .5px;
  }
  .brand__tagline { font-weight: 200; color: var(--white); }

  /* Front */
  .card--front .brand { left: 64px; top: 70px; gap: 22px; }
  .card--front .brand__mark { width: 104px; height: 104px; }
  .card--front .brand__name { font-size: 40px; }
  .card--front .brand__tagline { font-size: 15px; margin-top: 10px; }
  .service-pill {
    position: absolute;
    left: 50%;
    top: 212px;
    transform: translateX(-50%);
    border: 3px solid var(--orange);
    border-radius: 40px;
    padding: 6px 34px;
    color: var(--orange);
    font-weight: 600;
    font-size: 28px;
    letter-spacing: 1px;
    white-space: nowrap;
  }
  .service-lines {
    position: absolute;
    left: 0; right: 0;
    top: 290px;
    text-align: center;
    font-size: 24px;
    font-weight: 400;
    letter-spacing: .5px;
  }

  /* Back */
  .portrait {
    position: absolute;
    right: 0; top: 0;
    width: 330px; height: 100%;
    background: radial-gradient(ellipse 70% 65% at 60% 45%, var(--photo-light) 0%, var(--photo-mid) 55%, var(--card) 100%);
  }
  .card--back .brand { left: 36px; top: 34px; gap: 10px; }
  .card--back .brand__mark { width: 46px; height: 46px; }
  .card--back .brand__name { font-size: 17px; }
  .card--back .brand__tagline { font-size: 8px; margin-top: 3px; }
  .person { position: absolute; left: 60px; top: 132px; }
  .person__name { color: var(--orange); font-weight: 600; font-size: 28px; line-height: 1.1; }
  .person__role { font-size: 15px; font-weight: 300; margin-top: 2px; }
  .contact {
    position: absolute;
    left: 60px; top: 212px;
    list-style: none;
    font-size: 14px;
    font-weight: 300;
    line-height: 1;
  }
  .contact li { display: flex; align-items: center; gap: 10px; height: 23px; }
  .contact svg { width: 14px; height: 14px; fill: var(--orange); flex: none; }
</style>
</head>
<body>

  <section class="card card--front" aria-label="Visitenkarte Vorderseite">
    <div class="brand">
      <div class="brand__mark"></div>
      <div class="brand__text">
        <span class="brand__name">Falkos</span>
        <span class="brand__name">Kellnerservice</span>
        <span class="brand__tagline">…denn die nächste Feier kommt bestimmt!</span>
      </div>
    </div>
    <div class="service-pill">WAITER SERVICE</div>
    <p class="service-lines">Events, personnel service providers, festivals</p>
  </section>

  <section class="card card--back" aria-label="Visitenkarte Rückseite">
    <div class="portrait" role="img" aria-label="Porträtfoto des Inhabers in Weste und Hemd mit verschränkten Armen"></div>

    <div class="brand">
      <div class="brand__mark"></div>
      <div class="brand__text">
        <span class="brand__name">Falkos Kellnerservice</span>
        <span class="brand__tagline">…denn die nächste Feier kommt bestimmt!</span>
      </div>
    </div>

    <div class="person">
      <p class="person__name">Falko Brandtner</p>
      <p class="person__role">Inhaber</p>
    </div>

    <ul class="contact">
      <li>
        <svg viewBox="0 0 24 24"><path d="M6.6 10.8a15 15 0 0 0 6.6 6.6l2.2-2.2c.3-.3.7-.4 1-.2 1.1.4 2.3.6 3.6.6.6 0 1 .4 1 1V20c0 .6-.4 1-1 1A17 17 0 0 1 3 4c0-.6.4-1 1-1h3.5c.6 0 1 .4 1 1 0 1.3.2 2.5.6 3.6.1.3 0 .7-.2 1z"/></svg>
        02361 555 20 14
      </li>
      <li>
        <svg viewBox="0 0 24 24"><path d="M6.6 10.8a15 15 0 0 0 6.6 6.6l2.2-2.2c.3-.3.7-.4 1-.2 1.1.4 2.3.6 3.6.6.6 0 1 .4 1 1V20c0 .6-.4 1-1 1A17 17 0 0 1 3 4c0-.6.4-1 1-1h3.5c.6 0 1 .4 1 1 0 1.3.2 2.5.6 3.6.1.3 0 .7-.2 1z"/></svg>
        0176 555 38 71
      </li>
      <li>
        <svg viewBox="0 0 24 24"><path d="M12 2a10 10 0 1 0 0 20 10 10 0 0 0 0-20zm6.9 6h-3a15 15 0 0 0-1.3-3.9A8 8 0 0 1 18.9 8zM12 4c.8 1.2 1.5 2.5 1.9 4h-3.8c.4-1.5 1.1-2.8 1.9-4zM4.3 14a8 8 0 0 1 0-4h3.4a16 16 0 0 0 0 4zm.8 2h3a15 15 0 0 0 1.3 3.9A8 8 0 0 1 5.1 16zm3-8h-3a8 8 0 0 1 4.3-3.9C8.8 5.3 8.4 6.6 8.1 8zM12 20c-.8-1.2-1.5-2.5-1.9-4h3.8c-.4 1.5-1.1 2.8-1.9 4zm2.3-6H9.7a14 14 0 0 1 0-4h4.6a14 14 0 0 1 0 4zm.3 5.9c.6-1.2 1-2.5 1.3-3.9h3a8 8 0 0 1-4.3 3.9zm1.7-5.9a16 16 0 0 0 0-4h3.4a8 8 0 0 1 0 4z"/></svg>
        www.falkos-kellnerservice.de
      </li>
      <li>
        <svg viewBox="0 0 24 24"><path d="M2 5h20v2l-10 6L2 7zm0 4.3 10 6 10-6V19H2z"/></svg>
        info@falkos-kellnerservice.de
      </li>
      <li>
        <svg viewBox="0 0 24 24"><path d="M12 2a7 7 0 0 0-7 7c0 5.2 7 13 7 13s7-7.8 7-13a7 7 0 0 0-7-7zm0 9.5a2.5 2.5 0 1 1 0-5 2.5 2.5 0 0 1 0 5z"/></svg>
        Birkenweg 12, 45700 Lindtal
      </li>
      <li>
        <svg viewBox="0 0 24 24"><rect x="3" y="3" width="18" height="18" rx="3"/></svg>
        social: @falkoskellnerservice
      </li>
    </ul>
  </section>

</body>
</html>
```